Stylish business cards for KV7

To create an appealing and professional business card design for a WOMEN Owned Construction Supply Company.
2 sided card. Incorporate brand elements, curvy, colorful, sleek and bright. No solid white background. attached samples of styles added shapes/ribbons. Want something with that WOW that looks awesome, factor. It is a new logo, so feel free to mess with logo colors in the blue and teal factors that can look good with both dark and light background. If you want to try a watermark with just the KV7, without the "Supply" that might look cool to.

Industry/Entity Type

Women owned construction supply company

Contact Information for Business Card

Name, Title, and phone number and email, web page. maybe spot for qr code.

Font styles to use
Sans Serif

Requirements
Nice to have
• would love to see colors, maybe stylish ribbon dividers or some sort of 2 or 3 tone color card that compliments logo.
Should not have
• Please do not have all white background. Do not include Home/reale state/ or building images.

```html
<!DOCTYPE html>
<html lang="en">
<head>
<meta charset="utf-8">
<title>KV7 Supply – Business Card</title>
<link rel="stylesheet" href="https://fonts.googleapis.com/css2?family=Montserrat:wght@400;500;700&display=swap">
<style>
  :root {
    --stage: #1a1a1b;
    --card: #1c3858;
    --teal: #2b94bb;
    --ink: #f2f4f6;
    --font: "Montserrat", Arial, sans-serif;
  }
  * { margin: 0; padding: 0; box-sizing: border-box; }
  html, body { width: 1200px; height: 1059px; overflow: hidden; background: var(--stage); font-family: var(--font); }
  .stage { position: relative; width: 1200px; height: 1059px; }
  .card {
    position: absolute;
    background: var(--card);
    border-radius: 18px;
  }
  .card--front { left: 257px; top: 89px; width: 687px; height: 390px; }
  .card--back  { left: 254px; top: 547px; width: 693px; height: 393px; }

  .wordmark {
    position: absolute;
    left: 0; right: 0;
    text-align: center;
    color: var(--ink);
    font-weight: 700;
    letter-spacing: 1px;
    white-space: nowrap;
  }
  .card--front .wordmark { top: 92px; font-size: 44px; }
  .card--back .wordmark { top: 158px; font-size: 72px; }

  .holder {
    position: absolute;
    right: 371px; top: 244px;
    text-align: right;
  }
  .holder__name { color: var(--teal); font-weight: 700; font-size: 23px; letter-spacing: 0.3px; line-height: 1.1; }
  .holder__title { color: var(--ink); font-weight: 400; font-size: 15px; margin-top: 4px; }

  .divider {
    position: absolute;
    left: 342px; top: 233px;
    width: 1.5px; height: 69px;
    background: var(--teal);
  }

  .contacts {
    position: absolute;
    left: 366px; top: 230px;
    list-style: none;
  }
  .contacts li {
    display: flex; align-items: center;
    height: 27px;
    color: var(--ink);
    font-size: 15.5px;
    font-weight: 400;
  }
  .contacts svg { width: 13px; height: 13px; margin-right: 8px; flex: none; }

  .address {
    position: absolute;
    left: 0; right: 0; top: 333px;
    text-align: center;
    color: var(--ink);
    font-size: 15.5px;
    font-weight: 400;
  }
</style>
</head>
<body>
<main class="stage">
  <section class="card card--front" aria-label="Card front">
    <div class="wordmark">KV7 Supply</div>

    <div class="holder">
      <div class="holder__name">DANA HOLLIS</div>
      <div class="holder__title">CEO/Founder</div>
    </div>

    <div class="divider"></div>

    <ul class="contacts">
      <li>
        <svg viewBox="0 0 24 24" aria-hidden="true"><path fill="#2b94bb" d="M6.6 10.8a15.1 15.1 0 0 0 6.6 6.6l2.2-2.2a1 1 0 0 1 1-.25 11.4 11.4 0 0 0 3.6.57 1 1 0 0 1 1 1V20a1 1 0 0 1-1 1A17 17 0 0 1 3 4a1 1 0 0 1 1-1h3.5a1 1 0 0 1 1 1c0 1.25.2 2.45.57 3.57a1 1 0 0 1-.25 1z"/></svg>
        555.014.2718
      </li>
      <li>
        <svg viewBox="0 0 24 24" aria-hidden="true"><rect x="2" y="5" width="20" height="14" fill="#2b94bb"/><path d="M2 5l10 8 10-8" fill="none" stroke="#1c3858" stroke-width="1.8"/></svg>
        info@kv7supply.com.au
      </li>
      <li>
        <svg viewBox="0 0 24 24" aria-hidden="true" fill="none" stroke="#2b94bb" stroke-width="1.8"><circle cx="12" cy="12" r="10"/><ellipse cx="12" cy="12" rx="4.5" ry="10"/><path d="M2 12h20M4 7h16M4 17h16"/></svg>
        www.kv7supply.com.au
      </li>
    </ul>

    <p class="address">P.O Box 4410 Harbor Road Name Lakeview CD 12345</p>
  </section>

  <section class="card card--back" aria-label="Card back">
    <div class="wordmark">KV7 Supply</div>
  </section>
</main>
</body>
</html>
```